High-end executive coaching group needs a 2 page digital flyer

We need a 2 page digital flyer for a high end leadership coaching offering for global leaders in healthcare. The flyer will advertise a new service (an elite senior leadership coaching group) for senior leaders in the healthcare industry from around the world.
The flyer should be upmarket, professional and minimalist in style to meet the expectations of my professional market (very senior doctors and executives).
The design should be based on my existing logo and brand, see my landing page: www.marlowadvisory.com
The key elements needed are
1) An editable PDF which we can update as we revise the specific details of the offering. The text and draft design for this is attached.
2) The banner image should be high quality but abstract. It can be based on the landing page of my website (the two ripple effects) but does not need to strictly adhere to this.
3) The logo placement of the Marlow Advisory delta sign should be discreet so that it does not dominate
4) The small logos of our professional accrediting organisations should be discreetly placed at the end and should not dominate. They might work best as mono icons in a footer (e.g. blue on a white background, or white on blue.
5) Please find enclosed a previous flyer as an example of a similar style we have used for more junior professionals. The design worked quite well, although we now need a more upmarket version for our senior executives.

Please note this design specifically needs to use existing branding and images from my website: marlowadvisory.com. We are definitely not looking for stock "leadership team" images for this high-end brochure.

Target Market(s)

Senior global leaders in the healthcare industry

Industry/Entity Type

Leading business schools & Healthcare industry.

Font styles to use
Other font styles liked:
• Operetta (selective use for heading) and Sofia Pro (body text)

Colors
0054AA
0677BA
7BADD7
CADEEF
E8F1F8

Requirements
Must have
• Clean minimalist and high professionally look that directly speaks to the interests and perspectives of senior leader leaders in healthcare. It also needs very clear call to action sections
Nice to have
• Effective presentation of the two bios and photographs. These need to look impressive, but should not dominate.
Should not have
• Loud and bold colours, large use of logos.

```html
<!DOCTYPE html>
<html lang="en">
<head>
<meta charset="utf-8">
<title>Marlow Advisory – Elevate and Ignite Your Leadership</title>
<link rel="stylesheet" href="https://fonts.googleapis.com/css2?family=Playfair+Display:wght@400;700;800&family=Poppins:wght@300;400;500;600&display=swap">
<style>
  :root {
    --navy: #262f7e;
    --navy-deep: #1f276d;
    --accent: #3f63c9;
    --accent-band: #3550b4;
    --ink: #3a3f55;
    --muted: #5c6072;
    --paper: #ffffff;
    --backdrop: #e6e7ec;
    --badge-gold: #f2c94c;
    --badge-violet: #5b2c8e;
  }
  * { box-sizing: border-box; margin: 0; padding: 0; }
  html, body { width: 847px; height: 1200px; overflow: hidden; background: var(--backdrop); }
  body { position: relative; font-family: "Poppins", sans-serif; color: var(--ink); }

  /* each page is built at 847 × 1100 and set at 52% */
  .page { position: absolute; left: 203px; width: 847px; height: 1100px; overflow: hidden; background: var(--paper); transform: scale(0.52); transform-origin: 0 0; box-shadow: 0 4px 24px rgba(20,25,60,0.25); }
  .page-front { top: 19px; }
  .page-back { top: 610px; }

  .abs { position: absolute; }
  .serif { font-family: "Playfair Display", serif; }

  /* ---------- front ---------- */
  .hero-art { position: absolute; left: 0; top: 0; width: 847px; height: 402px; }
  .brand { left: 98px; top: 40px; width: 220px; text-align: center; }
  .brand-mark { display: inline-block; width: 24px; height: 24px; border-radius: 50%; background: var(--accent); margin-bottom: 22px; }
  .brand-name { font-family: "Playfair Display", serif; font-weight: 400; font-size: 30px; line-height: 1.02; color: var(--accent); }
  .headline { left: 48px; top: 188px; font-family: "Playfair Display", serif; font-weight: 800; font-size: 47px; line-height: 1.03; color: var(--navy); }
  .hero-band { left: 0; top: 347px; width: 466px; height: 55px; }
  .hero-tagline { left: 48px; top: 352px; width: 375px; font-size: 11.5px; line-height: 1.15; color: #fff; font-weight: 300; }

  .section-title { font-family: "Playfair Display", serif; font-weight: 700; font-size: 15px; color: var(--navy); margin-bottom: 8px; }
  .intro { left: 48px; top: 450px; width: 360px; }
  .intro p { font-size: 10.5px; line-height: 1.35; color: var(--muted); margin-bottom: 8px; font-weight: 300; }

  .testimonial { position: absolute; border-left: 1.5px solid var(--navy); border-bottom: 1.5px solid var(--navy); padding: 16px 14px 12px 14px; }
  .testimonial::before { content: ""; position: absolute; left: 22px; right: 0; top: 0; border-top: 1.5px solid var(--navy); }
  .testimonial::after { content: ""; position: absolute; right: 0; top: 0; bottom: 16px; border-right: 1.5px solid var(--navy); }
  .quote-open, .quote-close { position: absolute; font-family: "Playfair Display", serif; font-weight: 800; font-size: 30px; color: var(--accent); line-height: 1; }
  .quote-open { left: -6px; top: -12px; }
  .quote-close { right: -18px; bottom: -22px; }
  .testimonial p { font-size: 10.5px; line-height: 1.3; color: var(--muted); font-weight: 300; }
  .testimonial cite { display: block; text-align: right; font-style: normal; font-family: "Playfair Display", serif; font-size: 11px; color: var(--navy); margin-top: 10px; }
  .testimonial cite .who { color: var(--accent); }
  .testimonial-front { left: 57px; top: 586px; width: 340px; }

  .benefits { left: 443px; top: 450px; width: 360px; }
  .benefit { display: flex; gap: 12px; margin-bottom: 8px; }
  .benefit-icon { flex: none; width: 20px; height: 20px; border-radius: 3px; background: var(--navy); margin-top: 2px; }
  .benefit h3 { font-size: 11px; font-weight: 500; color: var(--accent); line-height: 1.25; }
  .benefit p { font-size: 10.5px; font-weight: 300; color: var(--muted); line-height: 1.25; }

  .schedule { left: 48px; top: 749px; width: 750px; display: flex; gap: 14px; }
  .schedule-item { flex: 1; height: 70px; background: var(--navy); border-radius: 2px; display: flex; align-items: center; gap: 14px; padding-left: 10px; color: #fff; font-family: "Playfair Display", serif; font-size: 17px; line-height: 1.2; }
  .schedule-item .tile { flex: none; width: 48px; height: 48px; background: #fff; border-radius: 8px; display: flex; align-items: center; justify-content: center; }
  .schedule-item .centered { flex: 1; text-align: center; padding-right: 14px; }

  .access { left: 48px; top: 851px; width: 750px; display: flex; gap: 14px; }
  .access-online { width: 336px; height: 52px; border: 1.5px solid var(--navy); border-radius: 4px; display: flex; align-items: center; gap: 12px; padding-left: 10px; font-family: "Playfair Display", serif; font-weight: 700; font-size: 13px; color: var(--navy); }
  .cost { flex: 1; height: 52px; border: 1.5px solid var(--navy); border-radius: 3px; position: relative; display: flex; align-items: flex-end; justify-content: center; padding-bottom: 9px; font-size: 11px; color: var(--navy); font-weight: 500; }
  .cost-label { position: absolute; top: 0; left: 8px; right: 8px; height: 16px; background: var(--navy); color: #fff; font-family: "Playfair Display", serif; font-size: 11px; text-align: center; line-height: 16px; }

  .cta-row { left: 48px; top: 938px; width: 750px; height: 44px; display: flex; align-items: center; }
  .cta-text { width: 300px; font-family: "Playfair Display", serif; font-weight: 700; font-size: 14px; line-height: 1.3; color: var(--navy); }
  .accredited { font-family: "Playfair Display", serif; font-weight: 700; font-size: 14px; color: var(--navy); margin-left: 33px; width: 140px; }

  .badges { display: flex; align-items: center; gap: 22px; }
  .badge-round { width: 44px; height: 44px; border-radius: 50%; border: 3px solid var(--navy); background: var(--badge-gold); }
  .badge-bar { width: 80px; height: 30px; border-radius: 3px; background: var(--navy); }
  .badge-tag { width: 66px; height: 26px; border-radius: 3px; background: var(--badge-violet); }

  .footer { position: absolute; left: 0; top: 1011px; width: 847px; height: 89px; background: var(--navy); color: #fff; }
  .footer-phone-bg { position: absolute; left: 0; top: 0; width: 340px; height: 89px; }
  .footer-phone { position: absolute; left: 48px; top: 26px; display: flex; align-items: center; gap: 10px; font-size: 24px; font-weight: 600; letter-spacing: 0.3px; }
  .footer-address, .footer-contacts { position: absolute; top: 22px; font-size: 12.5px; font-weight: 300; line-height: 1.5; }
  .footer-address { left: 360px; display: flex; gap: 8px; }
  .footer-contacts { left: 594px; }
  .footer-contacts div { display: flex; align-items: center; gap: 8px; }
  .round-icon { flex: none; width: 16px; height: 16px; border-radius: 50%; background: #fff; display: inline-flex; align-items: center; justify-content: center; margin-top: 2px; }

  /* ---------- back ---------- */
  .back-header { left: 0; top: 0; width: 847px; height: 114px; background: var(--navy); display: flex; align-items: center; justify-content: center; text-align: center; }
  .back-header h2 { font-family: "Playfair Display", serif; font-weight: 700; font-size: 22px; line-height: 1.25; letter-spacing: 0.4px; color: #fff; text-transform: uppercase; }

  .bio { top: 140px; width: 318px; }
  .bio-left { left: 47px; }
  .bio-right { left: 443px; }
  .bio-photo { display: block; width: 316px; height: 210px; border: 2px solid var(--accent); }
  .bio-name { margin-top: 22px; font-size: 15px; font-weight: 600; color: var(--accent); line-height: 1.2; }
  .bio-role { font-size: 11px; font-weight: 300; color: var(--ink); margin-top: 4px; }
  .bio-text { font-size: 10.3px; font-weight: 300; color: var(--muted); line-height: 1.4; margin-top: 12px; }

  .explore { left: 47px; top: 600px; width: 345px; }
  .explore h3 { font-family: "Playfair Display", serif; font-weight: 700; font-size: 14px; line-height: 1.35; color: var(--navy); }
  .explore ul { list-style: none; margin-top: 24px; }
  .explore li { position: relative; padding-left: 16px; font-size: 10px; font-weight: 300; color: var(--muted); line-height: 1.3; margin-bottom: 9px; }
  .explore li::before { content: ""; position: absolute; left: 2px; top: 5px; width: 5px; height: 5px; border-radius: 50%; background: var(--navy); }

  .discovery { left: 47px; top: 822px; width: 345px; }
  .discovery h3 { font-family: "Playfair Display", serif; font-weight: 700; font-size: 18px; color: var(--navy); margin-bottom: 14px; }
  .discovery div { display: flex; align-items: center; gap: 20px; font-size: 15px; font-weight: 300; color: var(--ink); margin-bottom: 10px; }
  .contact-dot { flex: none; width: 20px; height: 20px; border-radius: 50%; background: var(--accent); display: inline-flex; align-items: center; justify-content: center; }

  .limited { left: 449px; top: 600px; width: 330px; }
  .limited h3 { font-family: "Playfair Display", serif; font-weight: 700; font-size: 20px; color: var(--navy); margin-bottom: 8px; }
  .limited p { font-size: 15px; font-weight: 400; color: var(--ink); line-height: 1.3; }
  .testimonial-back { left: 458px; top: 722px; width: 310px; padding: 22px 22px 14px 22px; }
  .testimonial-back p { font-size: 10px; }
  .badges-back { left: 459px; top: 925px; }
</style>
</head>
<body>

<main class="page page-front">
  <svg class="hero-art" viewBox="0 0 847 402" aria-hidden="false">
    <defs>
      <linearGradient id="groupTone" x1="0" y1="0" x2="1" y2="1">
        <stop offset="0" stop-color="#d8d2cb"/>
        <stop offset="0.55" stop-color="#a49a90"/>
        <stop offset="1" stop-color="#4a423d"/>
      </linearGradient>
    </defs>
    <g role="img" aria-label="Photograph of a group of leaders seated in a circle in conversation">
      <polygon points="470,0 847,0 847,402 468,402 326,239" fill="url(#groupTone)"/>
    </g>
    <line x1="458" y1="0" x2="310" y2="239" stroke="var(--accent)" stroke-width="2.5"/>
  </svg>

  <div class="abs brand">
    <span class="brand-mark"></span>
    <div class="brand-name">Marlow<br>Advisory</div>
  </div>

  <h1 class="abs headline">Elevate and<br>Ignite Your<br>Leadership</h1>

  <svg class="abs hero-band" viewBox="0 0 466 55" aria-hidden="true">
    <polygon points="0,0 418,0 466,55 0,55" fill="var(--navy)"/>
  </svg>
  <p class="abs hero-tagline">Transformative conversations for senior healthcare leaders. Unlock purpose, engage authentically and amplify your leadership impact.</p>

  <section class="abs intro">
    <h2 class="section-title">Analytic Coaching Group for Senior Leaders</h2>
    <p>As a senior leader in healthcare, you're constantly navigating challenges. But where do you turn for authentic connections, reflection and personal growth?</p>
    <p>Rethink your leadership assumptions and approach challenges with fresh creativity. Secure your spot in our exclusive Analytic Coaching Group and ignite your leadership potential.</p>
  </section>

  <blockquote class="testimonial testimonial-front">
    <span class="quote-open">&ldquo;</span>
    <p>You bare your heart and share things you wouldn't under normal circumstances. You get to know each other very quickly. There's that sort of intense, shared experience that comes from speaking to each other's lives.</p>
    <cite><span class="who">Hannah</span>, Medical Director</cite>
    <span class="quote-close">&rdquo;</span>
  </blockquote>

  <section class="abs benefits">
    <h2 class="section-title">Benefits to you</h2>
    <div class="benefit"><span class="benefit-icon"></span><div><h3>Transformative conversations:</h3><p>Engage in discussions that spark innovative leadership</p></div></div>
    <div class="benefit"><span class="benefit-icon"></span><div><h3>Peer insights:</h3><p>Harness fresh insights from peers, enhancing your decision-making and effectiveness</p></div></div>
    <div class="benefit"><span class="benefit-icon"></span><div><h3>Reimagined leadership:</h3><p>Channel your creativity and redefine your leadership, personally and professionally</p></div></div>
    <div class="benefit"><span class="benefit-icon"></span><div><h3>Instant 360° insights:</h3><p>Gain real-time feedback from trusted peers to enrich your leadership</p></div></div>
    <div class="benefit"><span class="benefit-icon"></span><div><h3>Lead authentically:</h3><p>Develop effective strategies using the latest insights from group and leadership psychology</p></div></div>
  </section>

  <section class="abs schedule">
    <div class="schedule-item">
      <span class="tile"><svg width="30" height="30" viewBox="0 0 30 30" aria-hidden="true"><rect x="3" y="5" width="24" height="22" rx="2" fill="var(--accent)"/><rect x="3" y="5" width="24" height="6" fill="var(--navy)"/><g fill="#fff"><rect x="7" y="14" width="4" height="3"/><rect x="13" y="14" width="4" height="3"/><rect x="19" y="14" width="4" height="3"/><rect x="7" y="20" width="4" height="3"/><rect x="13" y="20" width="4" height="3"/><rect x="19" y="20" width="4" height="3"/></g></svg></span>
      <span>7 February 2024<br>11 December 2024</span>
    </div>
    <div class="schedule-item">
      <span class="tile"><svg width="30" height="30" viewBox="0 0 30 30" aria-hidden="true"><circle cx="15" cy="15" r="12" fill="var(--accent)"/><circle cx="15" cy="15" r="8.5" fill="#fff"/><path d="M15 9v6l4 3" stroke="var(--navy)" stroke-width="2" fill="none" stroke-linecap="round"/></svg></span>
      <span class="centered">7:30am - 8:45am<br>(UK time)</span>
    </div>
    <div class="schedule-item">
      <span class="tile"><svg width="30" height="30" viewBox="0 0 30 30" aria-hidden="true"><rect x="3" y="5" width="24" height="22" rx="3" fill="var(--accent)"/><rect x="6" y="13" width="18" height="10" rx="1" fill="#fff"/><text x="15" y="21" font-family="Poppins, sans-serif" font-size="7" font-weight="600" text-anchor="middle" fill="var(--navy)">WED</text></svg></span>
      <span class="centered">Wednesdays<br>every 2 weeks</span>
    </div>
  </section>

  <section class="abs access">
    <div class="access-online">
      <svg width="36" height="24" viewBox="0 0 36 24" aria-hidden="true"><rect x="0" y="2" width="24" height="20" rx="3" fill="var(--accent)"/><polygon points="25,12 35,4 35,20" fill="var(--accent)"/></svg>
      <span>Connect from anywhere by Meetline</span>
    </div>
    <div class="cost"><span class="cost-label">Cost:</span>£3350 [UK]</div>
    <div class="cost"><span class="cost-label">Cost:</span>£3350 [UK]</div>
    <div class="cost"><span class="cost-label">Cost:</span>$6530 [Australia]</div>
  </section>

  <section class="abs cta-row">
    <p class="cta-text">Secure your spot now and ignite your leadership potential..</p>
    <p class="accredited">Accredited by</p>
    <div class="badges">
      <span class="badge-round"></span>
      <span class="badge-bar"></span>
      <span class="badge-tag"></span>
    </div>
  </section>

  <footer class="footer">
    <svg class="footer-phone-bg" viewBox="0 0 340 89" aria-hidden="true"><polygon points="0,0 302,0 340,89 0,89" fill="var(--accent-band)"/></svg>
    <div class="footer-phone">
      <svg width="28" height="28" viewBox="0 0 28 28" aria-hidden="true"><circle cx="14" cy="14" r="12.5" fill="none" stroke="#fff" stroke-width="2"/><path d="M9.5 8.5l2.5-.5 1.5 3.5-1.6 1.2a8 8 0 0 0 3.4 3.4l1.2-1.6 3.5 1.5-.5 2.5c-5.5.6-10.6-4.5-10-10z" fill="#fff"/></svg>
      <span>+61 3 5550 2718</span>
    </div>
    <div class="footer-address">
      <span class="round-icon"><svg width="10" height="12" viewBox="0 0 10 12" aria-hidden="true"><path d="M5 0a4 4 0 0 1 4 4c0 3-4 8-4 8S1 7 1 4a4 4 0 0 1 4-4z" fill="var(--navy)"/><circle cx="5" cy="4" r="1.5" fill="#fff"/></svg></span>
      <span>PO Box 52 Hillview<br>Victoria 3400 Australia</span>
    </div>
    <div class="footer-contacts">
      <div><span class="round-icon"><svg width="10" height="8" viewBox="0 0 10 8" aria-hidden="true"><rect width="10" height="8" rx="1" fill="var(--navy)"/><path d="M0.5 1l4.5 3.5L9.5 1" stroke="#fff" fill="none"/></svg></span>info@marlowadvisory.com</div>
      <div><span class="round-icon"><svg width="11" height="11" viewBox="0 0 12 12" aria-hidden="true"><circle cx="6" cy="6" r="5" fill="none" stroke="var(--navy)" stroke-width="1.3"/><ellipse cx="6" cy="6" rx="2.2" ry="5" fill="none" stroke="var(--navy)"/><path d="M1 6h10" stroke="var(--navy)"/></svg></span>www.marlowadvisory.com</div>
    </div>
  </footer>
</main>

<main class="page page-back">
  <header class="abs back-header">
    <h2>Expertly guided by insight, academic rigour<br>and practical leadership strategies</h2>
  </header>

  <section class="abs bio bio-left">
    <svg class="bio-photo" viewBox="0 0 316 210" role="img" aria-label="Portrait photograph of Adrian Marlow outdoors">
      <defs><linearGradient id="bioToneA" x1="0" y1="0" x2="0" y2="1"><stop offset="0" stop-color="#9fb58a"/><stop offset="0.6" stop-color="#6e8a62"/><stop offset="1" stop-color="#2f3f78"/></linearGradient></defs>
      <rect width="316" height="210" fill="url(#bioToneA)"/>
    </svg>
    <h3 class="bio-name">ADRIAN MARLOW</h3>
    <p class="bio-role">Professor of Organisational Culture and Leadership</p>
    <p class="bio-text">Professor Adrian Marlow has 30 years' experience developing leaders. An award-winning business school professor, group analyst and psychoanalytic psychotherapist, he has taught senior leadership programmes at Westbury University, Kingsmere College London and the University of Southbank. His extensive leadership experience as a national health service clinical director and consultant psychotherapist inform his work as an IACP accredited executive coach. With a PhD from Regent College, University of Eastport, he is an expert in melding psychological insights with strategic organisational change.</p>
  </section>

  <section class="abs bio bio-right">
    <svg class="bio-photo" viewBox="0 0 316 210" role="img" aria-label="Portrait photograph of Dr Helen Ashcombe on a dark backdrop">
      <defs><radialGradient id="bioToneB" cx="0.5" cy="0.55" r="0.6"><stop offset="0" stop-color="#5a4038"/><stop offset="1" stop-color="#111111"/></radialGradient></defs>
      <rect width="316" height="210" fill="url(#bioToneB)"/>
    </svg>
    <h3 class="bio-name">DR HELEN ASHCOMBE</h3>
    <p class="bio-role">Consultant Psychiatrist, RSPP and Leadership</p>
    <p class="bio-text">Dr Helen Ashcombe is a renowned psychoanalyst, group analyst, consultant psychiatrist and organisational consultant in the health sector. She has 20 years of leadership within the national health service, and she was also the National Director of Therapies for the Meadowvale Group, directing therapy services across 100 UK hospitals. She holds prominent positions as Chair of the Patient Safety Group, Chair of the Working Group on the Effect of Suicide and Homicide on Psychiatrists, and Vice Chair of the Psychotherapy Faculty at the Royal Society of Psychiatric Practice.</p>
  </section>

  <section class="abs explore">
    <h3>Engage with global leaders, gain diverse insights and forge lasting bonds. Explore questions such as:</h3>
    <ul>
      <li>What kind of leader do I aspire to be in the next chapter of my life and career?</li>
      <li>What unique qualities and actions do I offer that no one else can?</li>
      <li>How can I galvanise my personal strengths to inspire and motivate others?</li>
    </ul>
  </section>

  <section class="abs discovery">
    <h3>Book your free discovery call</h3>
    <div><span class="contact-dot"><svg width="11" height="9" viewBox="0 0 10 8" aria-hidden="true"><rect width="10" height="8" rx="1" fill="#fff"/><path d="M0.5 1l4.5 3.5L9.5 1" stroke="var(--accent)" fill="none"/></svg></span>adrian@marlowadvisory.com</div>
    <div><span class="contact-dot"><svg width="11" height="9" viewBox="0 0 10 8" aria-hidden="true"><rect width="10" height="8" rx="1" fill="#fff"/><path d="M0.5 1l4.5 3.5L9.5 1" stroke="var(--accent)" fill="none"/></svg></span>helenashcombe@postbox.net</div>
    <div><span class="contact-dot"><svg width="12" height="12" viewBox="0 0 12 12" aria-hidden="true"><circle cx="6" cy="6" r="5" fill="none" stroke="#fff" stroke-width="1.3"/><ellipse cx="6" cy="6" rx="2.2" ry="5" fill="none" stroke="#fff"/><path d="M1 6h10" stroke="#fff"/></svg></span>www.marlowadvisory.com</div>
  </section>

  <section class="abs limited">
    <h3>Limited spots available</h3>
    <p>Don't miss this unique opportunity to transform your leadership journey.</p>
  </section>

  <blockquote class="testimonial testimonial-back">
    <span class="quote-open">&ldquo;</span>
    <p>Through this exceptional coaching, our leadership team elevated its performance to lead the hospital with greater clarity, cohesion and thoughtfulness. Not only do we provide a superior work environment for staff, but better care for our patients.</p>
    <cite><span class="who">John</span>, CEO</cite>
    <span class="quote-close">&rdquo;</span>
  </blockquote>

  <div class="abs badges badges-back">
    <span class="badge-round" style="width:54px;height:54px"></span>
    <span class="badge-bar"></span>
    <span class="badge-tag"></span>
  </div>

  <footer class="footer">
    <svg class="footer-phone-bg" viewBox="0 0 340 89" aria-hidden="true"><polygon points="0,0 302,0 340,89 0,89" fill="var(--accent-band)"/></svg>
    <div class="footer-phone">
      <svg width="28" height="28" viewBox="0 0 28 28" aria-hidden="true"><circle cx="14" cy="14" r="12.5" fill="none" stroke="#fff" stroke-width="2"/><path d="M9.5 8.5l2.5-.5 1.5 3.5-1.6 1.2a8 8 0 0 0 3.4 3.4l1.2-1.6 3.5 1.5-.5 2.5c-5.5.6-10.6-4.5-10-10z" fill="#fff"/></svg>
      <span>+61 3 5550 2718</span>
    </div>
    <div class="footer-address">
      <span class="round-icon"><svg width="10" height="12" viewBox="0 0 10 12" aria-hidden="true"><path d="M5 0a4 4 0 0 1 4 4c0 3-4 8-4 8S1 7 1 4a4 4 0 0 1 4-4z" fill="var(--navy)"/><circle cx="5" cy="4" r="1.5" fill="#fff"/></svg></span>
      <span>PO Box 52 Hillview<br>Victoria 3400 Australia</span>
    </div>
    <div class="footer-contacts">
      <div><span class="round-icon"><svg width="10" height="8" viewBox="0 0 10 8" aria-hidden="true"><rect width="10" height="8" rx="1" fill="var(--navy)"/><path d="M0.5 1l4.5 3.5L9.5 1" stroke="#fff" fill="none"/></svg></span>info@marlowadvisory.com</div>
      <div><span class="round-icon"><svg width="11" height="11" viewBox="0 0 12 12" aria-hidden="true"><circle cx="6" cy="6" r="5" fill="none" stroke="var(--navy)" stroke-width="1.3"/><ellipse cx="6" cy="6" rx="2.2" ry="5" fill="none" stroke="var(--navy)"/><path d="M1 6h10" stroke="var(--navy)"/></svg></span>www.marlowadvisory.com</div>
    </div>
  </footer>
</main>

</body>
</html>
```